BUSINESS CARD - HALLORAN FIELD SERVICES

I would like to create a business card for my fertilizer spreading business. I would like to incorporate my existing logo and also a description of the services offered. The business card will be given to farmers so must be kept simple but effective. It will also be left in stores so much also be eye catching in order to stand out from other cards.

Target Market(s)

FARMERS

Requirements
Must have
• FRONT OF CARD = EXISTING LOGO + "CUSTOMISED SPREADING" below the logo

REAR Of CARD = SERVICES OFFERED AND CONTACT DETAILS

- Bulk fertilizer including Lime, Gypsum, Manure & Compost
- Granular fertilizer including Single Super, Urea, Gran-am, & Custom Blends
- Modern equipment - Autosteer & Variable Rate Capable
- Friendly & Reliable Service
- Contact Gus: 0417 552 308
Nice to have
• utilize same color scheme as existing logo

```html
<!DOCTYPE html>
<html lang="en">
<head>
<meta charset="utf-8">
<title>Halloran Field Services – Business Card</title>
<link rel="stylesheet" href="https://fonts.googleapis.com/css2?family=Lato:ital,wght@0,400;0,700;0,900;1,400&family=Oswald:wght@500&display=swap">
<style>
  :root {
    --orange: #f7941d;
    --grey: #5b5b5d;
    --grey-dark: #4a4a4c;
    --white: #ffffff;
    --backdrop: #e6e6e8;
  }
  * { box-sizing: border-box; margin: 0; padding: 0; }
  html, body { width: 1200px; height: 1200px; overflow: hidden; }
  body {
    background: var(--backdrop);
    position: relative;
    font-family: "Lato", sans-serif;
    color: var(--grey);
  }
  .card {
    position: absolute;
    width: 480px;
    height: 839px;
    background: var(--white);
    overflow: hidden;
  }
  .card--front { left: 96px; top: 80px; }
  .card--back { left: 628px; top: 288px; }

  .brand { position: absolute; left: 0; right: 0; text-align: center; }
  .brand__mark {
    display: block;
    margin: 0 auto;
    border-radius: 50%;
    background: var(--grey);
  }
  .brand__name {
    font-family: "Lato", sans-serif;
    font-weight: 700;
    color: var(--grey);
    line-height: 1.1;
    letter-spacing: 0.5px;
  }
  .brand__rule {
    height: 3px;
    background: var(--orange);
    margin: 0 auto;
  }

  .card--front .brand { top: 30px; }
  .card--front .brand__mark { width: 160px; height: 160px; }
  .card--front .brand__name { font-size: 40px; margin-top: 18px; }
  .card--front .brand__rule { width: 390px; margin-top: 12px; }

  .headline {
    position: absolute;
    left: 0; right: 0;
    top: 372px;
    text-align: center;
    font-family: "Oswald", sans-serif;
    font-weight: 500;
    line-height: 1;
    text-transform: uppercase;
  }
  .headline__accent { display: block; color: var(--orange); font-size: 96px; }
  .headline__main { display: block; color: var(--grey-dark); font-size: 96px; margin-top: 8px; }

  .grass {
    position: absolute;
    left: 0; right: 0;
  }
  .card--front .grass {
    top: 592px; height: 120px;
    background: linear-gradient(to bottom, rgba(247,148,29,0.15), var(--orange) 90%);
  }
  .card--back .grass {
    top: 440px; height: 330px;
    background: linear-gradient(to bottom, rgba(91,91,93,0) 0%, rgba(91,91,93,0.35) 45%, var(--grey) 100%);
  }

  .contact {
    position: absolute;
    left: 0; right: 0; bottom: 0;
    background: var(--orange);
    display: flex;
    align-items: center;
    color: var(--white);
    font-family: "Lato", sans-serif;
    font-weight: 900;
    letter-spacing: 0.5px;
  }
  .card--front .contact { height: 128px; padding-left: 46px; font-size: 34px; }
  .card--back .contact { height: 70px; padding-left: 20px; font-size: 32px; }
  .contact__icon { flex: none; margin-right: 14px; }

  .card--back .brand { top: 30px; }
  .card--back .brand__mark { width: 110px; height: 110px; }
  .card--back .brand__name { font-size: 27px; margin-top: 12px; }
  .card--back .brand__rule { width: 220px; margin-top: 8px; }

  .services {
    position: absolute;
    left: 22px; top: 228px;
    list-style: none;
    z-index: 1;
  }
  .service {
    position: relative;
    padding-left: 40px;
    margin-bottom: 14px;
  }
  .service__icon { position: absolute; left: 0; top: 4px; }
  .service__title {
    color: var(--orange);
    font-weight: 700;
    font-size: 23px;
    line-height: 1.2;
    text-transform: uppercase;
  }
  .service__detail {
    font-size: 22px;
    line-height: 1.3;
    color: var(--grey);
  }
  .service__detail em { font-style: italic; }
</style>
</head>
<body>

  <section class="card card--front">
    <div class="brand">
      <span class="brand__mark"></span>
      <p class="brand__name">HALLORAN FIELD SERVICES</p>
      <div class="brand__rule"></div>
    </div>

    <h1 class="headline">
      <span class="headline__accent">Customized</span>
      <span class="headline__main">Spreading</span>
    </h1>

    <div class="grass" role="img" aria-label="Orange silhouette of tall pasture grass"></div>

    <div class="contact">
      <svg class="contact__icon" width="40" height="40" viewBox="0 0 40 40" aria-hidden="true">
        <circle cx="20" cy="20" r="20" fill="#5b5b5d"/>
        <path d="M14 11c1-1 2.5-1 3 0l2 3.5c.5 1 0 2-.8 2.5l-1.4 1c1 2.4 2.6 4 5 5l1-1.4c.6-.8 1.6-1.2 2.5-.7l3.5 2c1 .5 1 2 0 3l-1.6 1.6c-1.6 1.6-5 .8-8.6-2.7S10.8 15.6 12.4 14z" fill="#ffffff"/>
      </svg>
      <span>GUS 0417 552 308</span>
    </div>
  </section>

  <section class="card card--back">
    <div class="brand">
      <span class="brand__mark"></span>
      <p class="brand__name">HALLORAN FIELD SERVICES</p>
      <div class="brand__rule"></div>
    </div>

    <div class="grass" role="img" aria-label="Grey silhouette of wheat stalks and grass"></div>

    <ul class="services">
      <li class="service">
        <svg class="service__icon" width="30" height="18" viewBox="0 0 30 18" aria-hidden="true"><path d="M2 3l13 12L28 3" fill="none" stroke="#f7941d" stroke-width="5" stroke-linecap="round" stroke-linejoin="round"/></svg>
        <p class="service__title">Bulk Fertilizer</p>
        <p class="service__detail"><em>including</em> Lime, Gypsum,<br>Manure &amp; Compost</p>
      </li>
      <li class="service">
        <svg class="service__icon" width="30" height="18" viewBox="0 0 30 18" aria-hidden="true"><path d="M2 3l13 12L28 3" fill="none" stroke="#f7941d" stroke-width="5" stroke-linecap="round" stroke-linejoin="round"/></svg>
        <p class="service__title">Modern Equipment</p>
        <p class="service__detail">Autosteer &amp;<br>Variable Rate Capable</p>
      </li>
      <li class="service">
        <svg class="service__icon" width="30" height="18" viewBox="0 0 30 18" aria-hidden="true"><path d="M2 3l13 12L28 3" fill="none" stroke="#f7941d" stroke-width="5" stroke-linecap="round" stroke-linejoin="round"/></svg>
        <p class="service__title">Granular Fertilizer</p>
        <p class="service__detail"><em>including</em> Single Super, Urea,<br>Gran-am, &amp; Custom Blends</p>
      </li>
      <li class="service">
        <svg class="service__icon" width="30" height="18" viewBox="0 0 30 18" aria-hidden="true"><path d="M2 3l13 12L28 3" fill="none" stroke="#f7941d" stroke-width="5" stroke-linecap="round" stroke-linejoin="round"/></svg>
        <p class="service__title">Friendly &amp; Reliable<br>Services</p>
      </li>
    </ul>

    <div class="contact">
      <svg class="contact__icon" width="38" height="38" viewBox="0 0 40 40" aria-hidden="true">
        <circle cx="20" cy="20" r="20" fill="#5b5b5d"/>
        <path d="M14 11c1-1 2.5-1 3 0l2 3.5c.5 1 0 2-.8 2.5l-1.4 1c1 2.4 2.6 4 5 5l1-1.4c.6-.8 1.6-1.2 2.5-.7l3.5 2c1 .5 1 2 0 3l-1.6 1.6c-1.6 1.6-5 .8-8.6-2.7S10.8 15.6 12.4 14z" fill="#ffffff"/>
      </svg>
      <span>GUS 0417 552 308</span>
    </div>
  </section>

</body>
</html>
```